Business Card Design Project

We are not a new company, but renamed to "Vantorin Kitchens" last year. We specialize in modern high-end cabinetry imports. We would like to communicate a sense of quality and cutting edge technology. Ideally the design would incorporate our logo colors, silver, red and preferably a black, matte background. Though we are open to suggestions.
Logo is attached.
Edit: I have attached rough drafts of the previous cards, this way you will have all necessary content that needs to go on the cards.
Updates
Project Deadline Extended
Reason: We have received a lot of great designs, but due to the sheer number we couldn't respond to all. We will extend the deadline for another 7 days to finalize and provide feedback to designers.
Thank you for your hard work!
Industry/Entity Type
Business
Look and feel
Each slider illustrates characteristics of the customer's brand and the style your logo design should communicate.

```html
<!DOCTYPE html>
<html lang="en">
<head>
<meta charset="utf-8">
<title>Vantorin Kitchens – Business Card</title>
<link href="https://fonts.googleapis.com/css2?family=Roboto:wght@400;700&display=swap" rel="stylesheet">
<style>
  :root {
    --page: #e3e3e9;
    --card-black: #1b1b1d;
    --card-black-light: #2e2e31;
    --silver: #c8c8cc;
    --silver-dark: #8d8d92;
    --red: #e3202a;
    --white: #f2f2f2;
  }
  html, body {
    margin: 0;
    width: 1200px;
    height: 987px;
    overflow: hidden;
    background: var(--page);
    font-family: "Roboto", Arial, sans-serif;
  }
  .card {
    position: absolute;
    left: 220px;
    width: 760px;
    height: 434px;
    border-radius: 26px;
    overflow: hidden;
    background: radial-gradient(ellipse at 50% 35%, var(--card-black-light), var(--card-black) 75%);
    box-shadow: 0 10px 30px rgba(0,0,0,0.25);
  }
  .card-front { top: 50px; }
  .card-back { top: 503px; }

  .brand {
    position: absolute;
    left: 0; right: 0;
    display: flex;
    align-items: center;
    justify-content: center;
    gap: 16px;
    color: var(--silver);
    font-weight: 700;
    text-transform: uppercase;
    letter-spacing: 1px;
  }
  .brand-mark { background: var(--silver); }
  .card-front .brand { top: 70px; font-size: 46px; }
  .card-front .brand-mark { width: 34px; height: 34px; }
  .card-back .brand { top: 180px; font-size: 58px; }
  .card-back .brand-mark { width: 44px; height: 44px; }

  .contact {
    position: absolute;
    top: 175px;
    left: 0; right: 0;
    display: flex;
    justify-content: center;
    color: var(--white);
  }
  .person {
    text-align: right;
    padding-right: 22px;
    font-size: 19px;
    line-height: 26px;
  }
  .person-name { font-weight: 700; font-size: 22px; text-transform: uppercase; }
  .divider { width: 1px; background: var(--silver-dark); }
  .lines { padding-left: 22px; font-size: 21px; line-height: 28px; }
  .line { display: flex; align-items: center; gap: 8px; }
  .line svg { width: 16px; height: 16px; fill: var(--red); }

  .swoosh { position: absolute; left: 0; bottom: 0; width: 760px; height: 180px; }
</style>
</head>
<body>

<section class="card card-front">
  <div class="brand"><span class="brand-mark"></span>Vantorin Kitchens</div>

  <div class="contact">
    <div class="person">
      <div class="person-name">Marek Dolan</div>
      <div class="person-title">Director</div>
      <div class="person-address">2186 - 84 St. Edmonton</div>
      <div class="person-address">AB T6C 4R2</div>
    </div>
    <div class="divider"></div>
    <div class="lines">
      <div class="line">
        <svg viewBox="0 0 16 16"><path d="M3 1l3 3-2 2c1 2 3 4 5 5l2-2 3 3-2 3C6 15 1 10 1 3z"/></svg>
        780.555.0142
      </div>
      <div class="line">
        <svg viewBox="0 0 16 16"><path d="M1 15V6l7-5 7 5v9h-5v-5H6v5z"/></svg>
        780.555.0187
      </div>
      <div class="line">
        <svg viewBox="0 0 16 16"><path d="M4 0h8v16H4zM6 2v10h4V2z"/></svg>
        780.555.0163
      </div>
      <div class="line">
        <svg viewBox="0 0 16 16"><path d="M1 3h14v10H1zM2 4l6 5 6-5z"/></svg>
        marek@vantorinkitchens.ca
      </div>
    </div>
  </div>

  <svg class="swoosh" viewBox="0 0 760 180" preserveAspectRatio="none">
    <path d="M0 40 C200 40 420 110 760 150 L760 180 L0 180 Z" fill="#0b0b0c"/>
    <path d="M0 30 C220 28 430 100 760 140 L760 160 C430 122 220 52 0 52 Z" fill="var(--red)"/>
    <path d="M0 62 C220 64 430 132 760 168 L760 180 L0 180 Z" fill="var(--silver)"/>
    <path d="M0 62 C220 64 430 132 760 168 L760 172 C430 138 220 70 0 68 Z" fill="#0b0b0c"/>
  </svg>
</section>

<section class="card card-back">
  <div class="brand"><span class="brand-mark"></span>Vantorin Kitchens</div>
</section>

</body>
</html>
```